Quorbelline.io - Please redesign to make it look better from current design

We already have the current website, that you can access but we think it can improve from current version.
Quorbelline is a cryptocurrency hedge fund that allow you to participate in the hedge fund with cryptocurrency such as eth.
At current phase, we are doing an ICO, then we want to make sure that the website it looks professional, beautiful and trustable enough for investors after looking at our website.
Target Market(s)
Investors
Industry/Entity Type
Investment
Coding
Coded - Design and coding required
Number of Pages Required
1 page
Look and feel
Each slider illustrates characteristics of the customer's brand and the style your logo design should communicate.

```html
<!DOCTYPE html>
<html lang="en">
<head>
<meta charset="utf-8">
<title>Quorbelline – Digital Asset Management</title>
<link href="https://fonts.googleapis.com/css2?family=Poppins:wght@400;500;600;700&family=Open+Sans:wght@400;600&display=swap" rel="stylesheet">
<style>
:root{
  --blue:#0b57a6;
  --blue-deep:#0a4f9c;
  --accent:#2d9bd8;
  --ink:#2b2b2b;
  --text:#555;
  --muted:#888;
  --light:#f7f7f7;
  --white:#fff;
  --line:#e3e3e3;
}
*{box-sizing:border-box;margin:0;padding:0}
html,body{width:1200px;height:2521px;overflow:hidden;background:var(--white);font-family:"Open Sans",Arial,sans-serif;color:var(--text)}
.page{position:relative;width:1200px;height:2521px}
section,header,footer{position:absolute;left:0;width:1200px}
.abs{position:absolute}
.btn{position:absolute;display:flex;align-items:center;justify-content:center;background:var(--accent);color:var(--white);border-radius:22px;font-family:"Poppins",sans-serif;font-size:13px;font-weight:500}

/* header */
.site-header{top:0;height:131px;border-top:4px solid var(--blue);background:var(--white)}
.brand{left:131px;top:26px;display:flex;align-items:center;gap:10px;font-family:"Poppins",sans-serif;font-weight:600;font-size:24px;color:var(--blue-deep)}
.brand-dot{width:22px;height:22px;border-radius:50%;background:var(--blue-deep)}
.contact-tab{top:0;height:42px;background:var(--blue);color:var(--white);border-radius:0 0 24px 24px;display:flex;align-items:center;justify-content:center;gap:9px;font-size:15px}
.tab-phone{left:596px;width:202px}
.tab-mail{left:823px;width:227px}
.main-nav{top:91px;left:385px;display:flex;font-family:"Poppins",sans-serif;font-size:11.5px;font-weight:600;color:var(--ink)}
.main-nav a{position:absolute;white-space:nowrap;color:inherit;text-decoration:none}
.main-nav a.active{color:var(--accent)}
.search{left:882px;top:80px;width:185px;height:24px;border-bottom:1px solid var(--line);font-size:11px;color:#aaa;display:flex;align-items:center;justify-content:space-between}

/* hero */
.hero{top:131px;height:496px;background:radial-gradient(ellipse at 62% 45%,#4a4f58 0%,#1d2026 45%,#08090b 100%)}
.hero-media{left:560px;top:0;width:640px;height:496px;background:radial-gradient(circle at 35% 45%,rgba(190,160,90,.45) 0%,rgba(70,70,80,.25) 35%,transparent 70%)}
.hero h1{left:0;width:712px;top:150px;text-align:center;font-family:"Poppins",sans-serif;font-weight:600;font-size:35px;color:var(--white)}
.hero p{left:131px;width:450px;top:202px;text-align:center;font-family:"Poppins",sans-serif;font-size:13px;line-height:27px;color:var(--white)}
.hero .btn{left:291px;top:297px;width:131px;height:42px}
.dots{top:451px;left:570px;display:flex;gap:14px}
.dots span{width:10px;height:10px;border-radius:50%;border:1.5px solid #bbb}
.dots span.on{background:var(--accent);border-color:var(--accent)}

/* welcome */
.welcome{top:627px;height:492px;background:var(--light)}
.section-title{left:0;width:1200px;text-align:center;font-family:"Poppins",sans-serif;font-weight:500;font-size:27px;color:var(--ink)}
.welcome .section-title{top:50px}
.monitor-fill{border-radius:8px}
.welcome-media{left:131px;top:116px;width:381px;height:324px;background:linear-gradient(180deg,#2a2a2a 0%,#dfe3ea 8%,#c9a65a 50%,#e9ecf1 80%,#cfd2d6 100%)}
.welcome-copy{left:588px;top:120px;width:474px;font-size:11px;line-height:21px;color:var(--text)}
.welcome-copy p+p{margin-top:10px}
.welcome .btn{left:588px;top:374px;width:131px;height:42px}

/* team */
.team{top:1119px;height:481px;background:linear-gradient(180deg,rgba(16,92,170,.92),rgba(18,84,160,.9)),linear-gradient(90deg,#5a7ea8,#2f5f96)}
.team .section-title{top:70px;color:var(--white);font-weight:600}
.member{top:180px;width:292px;height:223px;border:1px solid rgba(255,255,255,.6);background:rgba(255,255,255,.12);color:var(--white);text-align:center}
.avatar{position:absolute;left:89px;top:-54px;width:114px;height:114px;border-radius:50%;border:2px solid var(--white);background:linear-gradient(180deg,#6b6f78,#3a3d44)}
.member h3{position:absolute;top:75px;width:100%;font-family:"Poppins",sans-serif;font-size:13.5px;font-weight:600}
.member .role{position:absolute;top:99px;width:100%;font-style:italic;font-size:12px}
.member .bio{position:absolute;top:121px;left:22px;right:22px;font-size:10.5px;line-height:20px}
.member .more{position:absolute;top:184px;width:100%;font-size:11px;text-decoration:underline}

/* process */
.process{top:1600px;height:509px;background:var(--white)}
.process .section-title{top:48px;font-weight:600}
.sub{left:131px;font-family:"Poppins",sans-serif;font-size:17px;color:var(--accent)}
.process-copy{left:131px;top:133px;width:510px;font-size:11px;line-height:21px}
.fee-list{left:131px;top:273px;list-style:none;font-size:11px;color:var(--text)}
.fee-list li{display:flex;align-items:center;height:32px;gap:14px}
.fee-list i{width:12px;height:12px;border-radius:50%;background:var(--accent);display:block}
.process-media{left:739px;top:88px;width:328px;height:328px;background:linear-gradient(180deg,#1b1b1b 0%,#f4f4f4 10%,#e0a62a 45%,#f4f4f4 75%,#c8ccd0 100%)}

/* cta */
.cta{top:2109px;height:122px;background:var(--blue-deep);color:var(--white)}
.cta h2{left:131px;top:27px;font-family:"Poppins",sans-serif;font-weight:600;font-size:24px}
.cta p{left:131px;top:60px;width:740px;font-size:11px;line-height:19px}
.cta .btn{left:899px;top:38px;width:163px;height:42px}

/* footer */
.site-footer{top:2231px;height:290px;background:var(--white)}
.footer-brand{left:131px;top:75px;display:flex;align-items:center;gap:12px;font-family:"Poppins",sans-serif;font-weight:600;font-size:28px;color:#9a9a9a}
.footer-brand span{width:26px;height:26px;border-radius:50%;background:#9a9a9a}
.f-col h4{font-family:"Poppins",sans-serif;font-weight:500;font-size:14px;color:var(--ink);margin-bottom:16px}
.f-col{top:40px;font-size:11px;color:var(--text)}
.links{left:380px;list-style:none}
.links li{height:23.5px}
.news{left:533px;width:230px;line-height:20px}
.news .input{margin-top:14px;width:221px;height:32px;border:1px solid var(--line);padding-left:10px;font-size:10.5px;color:#aaa;display:flex;align-items:center}
.news .btn{position:static;margin-top:15px;width:99px;height:34px;font-size:11px;font-weight:600}
.contact{left:828px;width:240px;font-size:12px}
.contact .row{display:flex;gap:14px;margin-bottom:18px;line-height:20px}
.contact svg{flex:none;margin-top:4px}
.rule{left:131px;top:230px;width:936px;height:1px;background:var(--line)}
.copyright{left:131px;top:252px;font-size:11px}
.follow{left:875px;top:246px;display:flex;align-items:center;gap:10px;font-size:11px}
.follow span.c{width:27px;height:27px;border-radius:50%;border:1.5px solid var(--accent)}
</style>
</head>
<body>
<div class="page">

<header class="site-header">
  <div class="abs brand"><span class="brand-dot"></span>Quorbelline</div>
  <div class="abs contact-tab tab-phone">
    <svg width="14" height="14" viewBox="0 0 24 24"><path fill="#fff" d="M6.6 10.8a15 15 0 0 0 6.6 6.6l2.2-2.2c.3-.3.7-.4 1-.2 1.1.4 2.3.6 3.6.6.6 0 1 .4 1 1V20c0 .6-.4 1-1 1A17 17 0 0 1 3 4c0-.6.4-1 1-1h3.5c.6 0 1 .4 1 1 0 1.3.2 2.5.6 3.6.1.3 0 .7-.2 1z"/></svg>
    +345-210-4486</div>
  <div class="abs contact-tab tab-mail">
    <svg width="15" height="12" viewBox="0 0 24 18"><path fill="#fff" d="M0 0h24v18H0z"/><path fill="none" stroke="#0b57a6" stroke-width="2" d="M1 1l11 8 11-8"/></svg>
    info@quorbelline.io</div>
  <nav class="abs main-nav">
    <a class="active" style="left:0">HOME</a>
    <a style="left:69px">ABOUT US</a>
    <a style="left:163px">SERVICES</a>
    <a style="left:253px">TEAM</a>
    <a style="left:321px">BLOG</a>
    <a style="left:388px">CONTACT US</a>
  </nav>
  <div class="abs search">Search
    <svg width="14" height="14" viewBox="0 0 24 24"><circle cx="10" cy="10" r="7" fill="none" stroke="#bbb" stroke-width="2"/><path d="M15 15l6 6" stroke="#bbb" stroke-width="2"/></svg>
  </div>
</header>

<section class="hero">
  <div class="abs hero-media" role="img" aria-label="Hand touching a tablet with stacked gold coins"></div>
  <h1 class="abs">Digital Asset Management</h1>
  <p class="abs">Quorbelline enable companies and investors to facilities business operation in modern digital world, including asset management on hedge fund strategy model...</p>
  <a class="btn">Learn More Info</a>
  <div class="abs dots"><span class="on"></span><span></span><span></span></div>
</section>

<section class="welcome">
  <h2 class="abs section-title">Welcome To Quorbelline</h2>
  <div class="abs welcome-media monitor-fill" role="img" aria-label="Desktop monitor showing a gold coin on a chart"></div>
  <div class="abs welcome-copy">
    <p>Quorbelline process and manages on hedge fund strategy models which invests in a diversified portfolio of blockchain tokens. Blockchain tokens are emerging which add a monetary incentive layer to p2p protocols and facilitate equity crowdfunding that anyone in the world can participate in. This means open source software developers can monetize their networks at the protocol level and users of the network are the equity owners of the network. For this conditions, returns will go to holders of the tokens.</p>
    <p>However, because of Cryptocurrency having almost 1,000 currencies and digital assets combine. The price is high volatility and hard for speculation or investing. Therefore, Quorbelline manages on hedge fund strategy models which speculate and invest in a diversified portfolio of blockchain tokens.The objective on this strategy...</p>
  </div>
  <a class="btn">Learn More Info</a>
</section>

<section class="team">
  <h2 class="abs section-title">Executive Team</h2>
  <article class="abs member" style="left:133px">
    <div class="avatar" role="img" aria-label="Portrait of the director"></div>
    <h3>Daniel Varenholt</h3>
    <div class="role">Director</div>
    <p class="bio">As a hedge fund manager, Varenholt is the Chief Executive Officer of Brightwater Capital LLC, an investment manager...</p>
    <div class="more">Learn More</div>
  </article>
  <article class="abs member" style="left:454px">
    <div class="avatar" role="img" aria-label="Portrait of the technical advisor"></div>
    <h3>Marco Lindqvist</h3>
    <div class="role">Technical advisor</div>
    <p class="bio">Lindqvist has various experienced on cryptocurrency and blockchain technology. He created what was the world's...</p>
    <div class="more">Learn More</div>
  </article>
  <article class="abs member" style="left:773px">
    <div class="avatar" role="img" aria-label="Portrait of the marketing consultant"></div>
    <h3>Kenji Aldermont</h3>
    <div class="role">Marketing Consultant</div>
    <p class="bio">Aldermont embeds a decade of experience in brand building, strategic planning, and marketing...</p>
    <div class="more">Learn More</div>
  </article>
</section>

<section class="process">
  <h2 class="abs section-title">Process</h2>
  <h3 class="abs sub" style="top:104px">Hedge Fund Model</h3>
  <p class="abs process-copy">Quorbelline run on closed-end fund （CEF）model which offers its shares to investors and utilize the fund to speculate and invest in the innovative blockchain tokens. Quorbelline will charge an upfront annual operation fee 4% of the money raised during the ICO. After that, the fund will charge a quarterly performance of 50% on the net profit made</p>
  <h3 class="abs sub" style="top:240px">Net Profit Distribution</h3>
  <ul class="abs fee-list">
    <li><i></i>50 % of net profit is distributed to investors</li>
    <li><i></i>0 – 5 % net profit &gt; 0% performance fee</li>
    <li><i></i>5 – 10% net profit &gt; 5% performance fee</li>
    <li><i></i>10-15 % net profit &gt; 13% performance fee</li>
    <li><i></i>&gt; 15% net profit &gt; 15% performance fee</li>
    <li><i></i>The remainder （50% minus performance fee, so at least 35%）is reinvested</li>
  </ul>
  <div class="abs process-media monitor-fill" role="img" aria-label="Desktop monitor showing a coin with a rising chart arrow"></div>
</section>

<section class="cta">
  <h2 class="abs">FOR MORE INFORMATION</h2>
  <p class="abs">Aliquip ex ea commodo consequat. Duis aute irure dolor in reprehenderit in voluptate velit esse cillum dolore eu fugiat nulla pariatur. Excepteur sint occaecat cupidatat non proident, sunt in culpa qui officia...</p>
  <a class="btn">Download Whitepaper</a>
</section>

<footer class="site-footer">
  <div class="abs footer-brand"><span></span>Quorbelline</div>
  <div class="abs f-col links-col" style="left:380px">
    <h4>Quick Links</h4>
    <ul class="links" style="list-style:none">
      <li>Home</li><li>About us</li><li>Services</li><li>Team</li><li>Blog</li><li>Contact</li>
    </ul>
  </div>
  <div class="abs f-col news">
    <h4>Newsletter</h4>
    <p>Register your Email Address to get Information about us</p>
    <div class="input">Email Address</div>
    <a class="btn">SUBSCRIBE</a>
  </div>
  <div class="abs f-col contact">
    <h4>Contact Info</h4>
    <div class="row"><svg width="10" height="14" viewBox="0 0 10 14"><path fill="#2d9bd8" d="M5 0a5 5 0 0 1 5 5c0 4-5 9-5 9S0 9 0 5a5 5 0 0 1 5-5z"/><circle cx="5" cy="5" r="2" fill="#fff"/></svg><span style="font-size:11px">Suite 12-04, 9/F., North Wing, Harbour Trade Centre</span></div>
    <div class="row"><svg width="13" height="13" viewBox="0 0 24 24"><path fill="#2d9bd8" d="M6.6 10.8a15 15 0 0 0 6.6 6.6l2.2-2.2c.3-.3.7-.4 1-.2 1.1.4 2.3.6 3.6.6.6 0 1 .4 1 1V20c0 .6-.4 1-1 1A17 17 0 0 1 3 4c0-.6.4-1 1-1h3.5c.6 0 1 .4 1 1 0 1.3.2 2.5.6 3.6.1.3 0 .7-.2 1z"/></svg><span>+345-210-4486</span></div>
    <div class="row"><svg width="14" height="11" viewBox="0 0 24 18"><path fill="#2d9bd8" d="M0 0h24v18H0z"/><path fill="none" stroke="#fff" stroke-width="2" d="M1 1l11 8 11-8"/></svg><span>info@quorbelline.io</span></div>
  </div>
  <div class="abs rule"></div>
  <div class="abs copyright">Copyright © 2017, quorbelline | All rights reserved.</div>
  <div class="abs follow">Follow Us :<span class="c"></span><span class="c"></span><span class="c"></span><span class="c"></span></div>
</footer>

</div>
</body>
</html>
```